Web Design

We need a website for a company based in Doha Qatar called
Lumara Maid Service.

It is the number one maid cleaning service company, and we have branches all over qatar.

Luxury Cleaning Service Provider.

The color scheme is gold, yellow and black like the logo.

Before they get to the website, there is an intro video.

The website should depict luxury.

Target Market(s)

People who need maids at their houses.

Industry/Entity Type

Cleaning Service

Requirements
Must have
• Luxury, Sleek, Modern

The opening sequence is a video which I already have. Its too big to upload here so I am going to put it on youtube.

After the opening sequence, the home page should have a widescreen photo background and it should change every five seconds, the first background photo should be of qatar westbay skyline. Then the second background should be of maid photos in cleaning positions. Then the third background should be of cleaner photos etc.

We will send you all the tabs and all the content later.

```html
<!DOCTYPE html>
<html lang="en">
<head>
<meta charset="utf-8">
<title>Lumara Maid Service</title>
<link rel="stylesheet" href="https://fonts.googleapis.com/css2?family=Oswald:wght@300&family=Roboto+Condensed:wght@400&family=Mulish:wght@400;600&display=swap">
<style>
  :root {
    --bar: #181818;
    --gold: #e8b90f;
    --gold-soft: #f0c419;
    --nav-grey: #9a9a9a;
    --foot-grey: #a8a8a8;
    --white: #ffffff;
    --sky-top: #5f7a9c;
    --sky-mid: #9fb2c6;
    --city: #7d8a93;
    --water: #3c5560;
  }
  * { margin: 0; padding: 0; box-sizing: border-box; }
  html, body { width: 1200px; height: 851px; overflow: hidden; background: var(--bar); }
  .page { position: relative; width: 1200px; height: 851px; }

  .site-header { position: absolute; left: 0; top: 0; width: 1200px; height: 112px; background: var(--bar); }
  .brand { position: absolute; left: 84px; top: 40px; display: flex; align-items: center; gap: 9px;
    font-family: "Mulish", sans-serif; font-weight: 600; font-size: 16px; color: var(--gold); letter-spacing: 0.3px; }
  .brand-dot { width: 22px; height: 22px; border-radius: 50%; background: var(--gold); }
  .main-nav { position: absolute; top: 45px; left: 0; width: 1200px; height: 22px;
    font-family: "Mulish", sans-serif; font-size: 15px; }
  .main-nav a { position: absolute; transform: translateX(-50%); color: var(--nav-grey); text-decoration: none; white-space: nowrap; }
  .main-nav a.active { color: var(--gold-soft); }

  .hero { position: absolute; left: 0; top: 112px; width: 1200px; height: 661px; overflow: hidden; }
  .hero-photo { position: absolute; inset: 0;
    background: linear-gradient(180deg, var(--sky-top) 0%, var(--sky-mid) 35%, var(--city) 58%, var(--water) 72%, #2c434d 100%); }
  .hero-title { position: absolute; left: 0; width: 1200px; text-align: center; white-space: nowrap;
    font-family: "Oswald", sans-serif; font-weight: 300; line-height: 1; text-transform: uppercase; }
  .hero-title.welcome { top: 124px; font-size: 80px; color: var(--gold); }
  .hero-title.company { top: 222px; font-size: 96px; color: var(--white); }
  .slide-arrow { position: absolute; top: 301px; width: 62px; height: 62px; }
  .slide-arrow.prev { left: 46px; }
  .slide-arrow.next { left: 1089px; }

  .feature { position: absolute; top: 372px; width: 280px; text-align: center; }
  .feature-badge { display: block; width: 103px; height: 103px; border-radius: 50%; background: var(--gold); margin: 0 auto; }
  .feature-title { margin-top: 15px; font-family: "Roboto Condensed", sans-serif; font-weight: 400; font-size: 18px; color: var(--gold-soft); }
  .feature-text { margin-top: 9px; font-family: Arial, sans-serif; font-size: 12px; line-height: 23.5px; color: var(--white); }

  .site-footer { position: absolute; left: 0; top: 773px; width: 1200px; height: 78px; background: var(--bar); }
  .copyright { position: absolute; left: 33px; top: 33px; font-family: "Mulish", sans-serif; font-size: 11.5px; color: var(--foot-grey); }
  .social { position: absolute; left: 980px; top: 24px; }
</style>
</head>
<body>
<div class="page">
  <header class="site-header">
    <div class="brand"><span class="brand-dot"></span>Lumara Maid Service</div>
    <nav class="main-nav">
      <a class="active" style="left:429px" href="#">Home</a>
      <a style="left:556px" href="#">About Us</a>
      <a style="left:690px" href="#">Services</a>
      <a style="left:807px" href="#">Blog</a>
      <a style="left:924px" href="#">Videos</a>
      <a style="left:1061px" href="#">Contact US</a>
    </nav>
  </header>

  <section class="hero">
    <div class="hero-photo" role="img" aria-label="Photo of the Doha West Bay skyline over the water"></div>
    <h1 class="hero-title welcome">Welcome to</h1>
    <h2 class="hero-title company">Lumara Maid Service</h2>

    <svg class="slide-arrow prev" viewBox="0 0 62 62" aria-label="Previous slide">
      <circle cx="31" cy="31" r="29" fill="rgba(255,255,255,0.08)" stroke="#e6e6e6" stroke-width="2.5"/>
      <path d="M40 17 L20 31 L40 45 L35 31 Z" fill="#d9d9d9"/>
    </svg>
    <svg class="slide-arrow next" viewBox="0 0 62 62" aria-label="Next slide">
      <circle cx="31" cy="31" r="29" fill="rgba(255,255,255,0.08)" stroke="#e6e6e6" stroke-width="2.5"/>
      <path d="M22 17 L42 31 L22 45 L27 31 Z" fill="#d9d9d9"/>
    </svg>

    <div class="feature" style="left:139px">
      <span class="feature-badge" role="img" aria-label="Cleaning equipment icon"></span>
      <h3 class="feature-title">Neque porro quisquam est qui</h3>
      <p class="feature-text">It is a long established fact that a reader will be<br>distracted by the readable content of a pag<br>when looking at its layout.</p>
    </div>
    <div class="feature" style="left:462px">
      <span class="feature-badge" role="img" aria-label="Maid with broom icon"></span>
      <h3 class="feature-title">Neque porro quisquam est qui</h3>
      <p class="feature-text">It is a long established fact that a reader will be<br>distracted by the readable content of a pag<br>when looking at its layout.</p>
    </div>
    <div class="feature" style="left:786px">
      <span class="feature-badge" role="img" aria-label="Duster sweeping icon"></span>
      <h3 class="feature-title">Neque porro quisquam est qui</h3>
      <p class="feature-text">It is a long established fact that a reader will be<br>distracted by the readable content of a pag<br>when looking at its layout.</p>
    </div>
  </section>

  <footer class="site-footer">
    <p class="copyright">Copy Rights 2014 Lumara Maid Service. All Rights Reserved.</p>
    <svg class="social" width="152" height="34" viewBox="0 0 152 34" aria-label="Social links">
      <circle cx="17" cy="17" r="15.5" fill="none" stroke="#9a9a9a" stroke-width="1.5"/>
      <circle cx="56" cy="17" r="15.5" fill="none" stroke="#9a9a9a" stroke-width="1.5"/>
      <circle cx="95" cy="17" r="15.5" fill="none" stroke="#9a9a9a" stroke-width="1.5"/>
      <circle cx="135" cy="17" r="15.5" fill="none" stroke="#9a9a9a" stroke-width="1.5"/>
    </svg>
  </footer>
</div>
</body>
</html>
```